Buch-/eBook-Cover für Traumatherapeutin
Zielgruppe
Ich bin Traumatherapeutin und schreibe ein Buch zum Thema Trauma bearbeiten.
Meine Zielgruppe sucht Heilung, Genesung, Selbstliebe etc.
Aufgabenstellung
Buchcover
Bitte erstell mir ein modernes positives inspirierendes Buchcover mit dem
Titel: 'Morgenlicht NEU entdecken“
Untertitel: „Spüre den Mut der ganz in dir wohnt“
Dr. Mira Kessow
Ich hätte gerne ein modernes Buch, das entweder einen Bezug zum Thema Trauma hat oder aber einfach stylische Schriftzüge. Bin aber auch offen für andere Vorschläge.
Dunkelblau, weiß und türkis oder auch rosa mag ich ganz gerne. Wobei Dunkelblau, weiß und türkis meine Favoriten sind und mit rosa höchstens kleinere Akzente gesetzt werden sollten.
Das Buchcover soll modern sein und direkt ansprechen. Gerne eine originelle Lösung, oder etwas Besonderes, etwas das Tiefe ausdrückt, oder man mehrmals hinsehen muss um etwas zu erkennen oder etwas das mehr Interpretationsspielraum lässt.
Gerne auch viel weiß, zumindest heller und nicht zu dunkel. Stylish, aber nicht überfrachtet.
Schreib mich gerne an, wenn du Fragen hast.
Ich habe mal zwei Beispiel von Typolösungen angehängt, die ich ganz cool fände.
Ich freue mich auf deine Ideen :-)
Ganz liebe Grüße
Mira

```html
<!DOCTYPE html>
<html lang="de">
<head>
<meta charset="utf-8">
<title>Morgenlicht NEU entdecken – Buchcover</title>
<link rel="stylesheet" href="https://fonts.googleapis.com/css2?family=Playfair+Display:wght@500;600&family=Montserrat:ital,wght@1,500&family=Saira:ital,wght@1,400&family=Open+Sans:wght@400&display=swap">
<style>
  :root {
    --stage: #7479a8;
    --sand: #d9d3c7;
    --sky-light: #8cc0d6;
    --turquoise: #62a7c6;
    --deep-water: #3b6a89;
    --lagoon: #5a9dbd;
    --gold-light: #ffd866;
    --gold: #e8a916;
    --gold-dark: #b97a08;
    --white: #ffffff;
    --wing: #7fb3cf;
  }
  * { margin: 0; padding: 0; box-sizing: border-box; }
  html, body { width: 1200px; height: 960px; overflow: hidden; }
  body {
    background: var(--stage);
    display: flex;
    align-items: center;
    justify-content: center;
  }
  .cover {
    position: relative;
    width: 600px;
    height: 870px;
    overflow: hidden;
    background: linear-gradient(180deg,
      var(--sand) 0%,
      var(--sky-light) 12%,
      var(--turquoise) 35%,
      var(--lagoon) 52%,
      var(--deep-water) 58%,
      var(--lagoon) 72%,
      var(--turquoise) 88%,
      var(--sky-light) 100%);
  }
  .horizon-line {
    position: absolute;
    left: 0; right: 0;
    top: 505px;
    height: 3px;
    background: linear-gradient(90deg, rgba(255,255,255,0.1), rgba(255,255,255,0.75) 40%, rgba(255,255,255,0.35));
    transform: rotate(1.5deg);
  }
  .illustration {
    position: absolute;
    border-radius: 50%;
    background: radial-gradient(ellipse at center, rgba(120,170,200,0.7) 0%, rgba(90,150,185,0.35) 50%, rgba(90,150,185,0) 75%);
  }
  .illustration--top { left: 130px; top: 10px; width: 350px; height: 290px; }
  .illustration--bottom { left: 85px; top: 690px; width: 200px; height: 170px; }
  .title {
    position: absolute;
    left: 0; right: 0;
    top: 245px;
    text-align: center;
  }
  .title span {
    display: block;
    background: linear-gradient(180deg, var(--gold-light) 0%, var(--gold) 55%, var(--gold-dark) 100%);
    -webkit-background-clip: text;
    background-clip: text;
    color: transparent;
    filter: drop-shadow(2px 3px 3px rgba(20,40,70,0.35));
  }
  .title__serif {
    font-family: "Playfair Display", serif;
    font-weight: 600;
    letter-spacing: -1px;
    line-height: 1;
  }
  .title__line-one { font-size: 96px; }
  .title__accent {
    font-family: "Montserrat", sans-serif;
    font-style: italic;
    font-weight: 500;
    font-size: 80px;
    line-height: 1.05;
    margin: 6px 0 4px;
  }
  .title__line-three { font-size: 106px; }
  .subtitle {
    position: absolute;
    right: 30px;
    top: 670px;
    text-align: right;
    font-family: "Saira", sans-serif;
    font-style: italic;
    font-size: 36px;
    line-height: 1.45;
    color: var(--white);
    text-shadow: 1px 2px 3px rgba(20,40,70,0.35);
  }
  .author {
    position: absolute;
    left: 0; right: 0;
    top: 840px;
    padding-left: 10px;
    text-align: center;
    font-family: "Open Sans", sans-serif;
    font-size: 17px;
    color: var(--white);
  }
</style>
</head>
<body>
  <div class="cover">
    <div class="horizon-line"></div>
    <div class="illustration illustration--top" role="img" aria-label="Illustration einer blauen Libelle im Flug"></div>
    <div class="illustration illustration--bottom" role="img" aria-label="Illustration einer kleinen blauen Libelle"></div>
    <h1 class="title">
      <span class="title__serif title__line-one">Morgenlicht</span>
      <span class="title__accent">NEU</span>
      <span class="title__serif title__line-three">entdecken</span>
    </h1>
    <p class="subtitle">Spüre den Mut<br>der ganz in dir wohnt</p>
    <p class="author">Dr. Mira Kessow</p>
  </div>
</body>
</html>
```